KELBRIDGE PAINTING

We are a painting company. We paint residential, commercial and strata jobs. I need the website to be very sharp, neat and elegant. I've attached our logo. the Logo needs to be embossed as a gold color and the background like a Matt black. I need these tabs:

• HOME • ABOUT US • SERVICES • TESTIMONIALS • SHOWCASE • CONTACT US

Be creative and innovative in your style.
take this as an example to just get the gist of what I'm expecting. If you can better it then the job is yours!

http://rickhalvorpainting.com.au/contact.html

I look forward to seeing your artwork :)

#These are the links to my logo in PSD format.

https://www.filevaultzy.com/s/qwertplk83nd7ha/Kelbridge%20Painting%20Luxury%20Gold.rar

https://www.filevaultzy.com/sh/bzuyrak2m5wqp9/QoPL7-xvMn

Painting

• Making the Logo embossed like the artworks i have attached is definitely a necessity.

Can you let me know if this is possible to apply to the website.

thank you

```html
<!DOCTYPE html>
<html lang="en">
<head>
<meta charset="utf-8">
<title>Kelbridge Painting</title>
<link rel="stylesheet" href="https://fonts.googleapis.com/css2?family=Crimson+Text:wght@400;600&family=Noto+Sans:ital,wght@0,400;0,700;1,400&display=swap">
<style>
:root{
  --bar-blue:#1d6a8f;
  --link-blue:#1a7fb0;
  --head-blue:#1a8bc0;
  --panel-blue:rgba(34,70,150,.88);
  --gold:#f2b61c;
  --gold-light:#f7d163;
  --text-grey:#7a7a7a;
  --brand-ink:#3a3a3a;
  --footer-bg:#3a3a3a;
  --footer-text:#d8d8d8;
  --white:#ffffff;
}
*{margin:0;padding:0;box-sizing:border-box}
html,body{width:859px;height:1200px;overflow:hidden;background:var(--white)}
body{position:relative;font-family:"Noto Sans",sans-serif;color:var(--text-grey)}
h2,h3{font-weight:400}
.abs{position:absolute}

/* header */
.top-bar{left:0;top:0;width:859px;height:10px;background:var(--bar-blue)}
.header{left:0;top:10px;width:859px;height:117px;background:var(--white)}
.brand-name{left:45px;top:54px;font-size:12px;font-weight:400;color:var(--brand-ink);letter-spacing:.8px}
.brand-tag{left:45px;top:73px;font-size:7px;color:var(--text-grey);letter-spacing:.4px}
.nav a{position:absolute;top:64px;font-size:11.5px;color:var(--link-blue);text-decoration:none;letter-spacing:.6px}
.nav a.active{left:260px;top:58px;width:52px;height:24px;line-height:24px;text-align:center;background:var(--link-blue);color:var(--white);border-radius:3px}

/* hero */
.hero{left:0;top:127px;width:859px;height:455px;background:linear-gradient(180deg,#1f3f8e 0%,#3a77c7 45%,#a9cbe9 80%,#d8b24a 91%,#c9913a 100%)}
.service{position:absolute;width:118px;text-align:center}
.service-label{font-family:"Crimson Text",serif;font-size:13.5px;color:var(--white);letter-spacing:.8px;margin-bottom:7px}
.service-photo{width:118px;height:118px;border-radius:50%;border:3px solid var(--white)}
.welcome{left:362px;top:363px;width:497px;height:151px;background:var(--panel-blue)}
.welcome-kicker{left:34px;top:17px;font-family:"Crimson Text",serif;font-variant:small-caps;font-size:15px;color:var(--white);letter-spacing:1.5px;line-height:1}
.welcome-title{left:34px;top:31px;font-family:"Crimson Text",serif;font-variant:small-caps;font-size:21px;color:var(--gold);letter-spacing:1.8px;line-height:1}
.welcome-rule{left:34px;top:56px;width:387px;height:2px;border-top:1px solid rgba(255,255,255,.5);border-bottom:1px solid rgba(255,255,255,.2)}
.welcome-text{left:32px;top:70px;width:400px;font-size:9.5px;line-height:20px;color:var(--white);letter-spacing:.4px}
.dots{left:54px;display:flex;gap:3px}
.dots span{width:9px;height:9px;border-radius:50%;background:#6b5a2a}
.dots span:first-child{background:#222}

/* testimonials */
.testimonials{left:0;top:582px;width:859px;height:199px;background:linear-gradient(180deg,#f2f2f2,#dcdcdc)}
.section-title{left:118px;top:22px;font-family:"Crimson Text",serif;font-size:18px;color:var(--head-blue);letter-spacing:1.2px}
.section-rule{left:120px;top:50px;width:636px;height:3px;border-top:1px solid #bbb;border-bottom:1px solid #ddd}
.quote-photo{width:74px;height:64px;border:3px solid var(--white);box-shadow:0 0 2px rgba(0,0,0,.2)}
.quote-text{width:200px;font-size:9px;line-height:16px;color:#666;text-align:justify;letter-spacing:.1px}
.quote-author{font-size:9px;font-style:italic;color:var(--head-blue);text-align:right;width:200px;letter-spacing:.3px}

/* guarantee */
.guarantee-area{left:0;top:781px;width:859px;height:197px;background:#f4f4f4}
.guarantee{left:111px;top:29px;width:649px;height:141px;background:#e8e7e5;border-radius:4px;box-shadow:0 12px 14px -10px rgba(0,0,0,.25)}
.guarantee-head{left:0;top:0;width:649px;height:27px;background:linear-gradient(180deg,var(--gold-light),#efbf3d);border-radius:4px 4px 0 0}
.guarantee-title{left:19px;top:2px;font-family:"Crimson Text",serif;font-size:17px;color:var(--white);letter-spacing:1px}
.guarantee-text{left:9px;top:53px;width:515px;font-size:9.5px;line-height:16.8px;color:#888;letter-spacing:.3px}
.seal{left:543px;top:38px;width:72px;height:72px;border-radius:50%;background:radial-gradient(circle,#f5cf4a,#d9a21a);box-shadow:1px 2px 4px rgba(0,0,0,.3)}

/* footer */
.footer{left:0;top:978px;width:859px;height:222px;background:var(--footer-bg)}
.footer-title{font-family:"Crimson Text",serif;font-size:16px;color:var(--white);letter-spacing:1.2px}
.footer-rule{height:1px;background:#6a6a6a}
.field{background:var(--white);border-radius:3px;font-size:9.5px;color:#e08a2a;padding:5px 9px}
.submit{left:115px;top:180px;width:64px;height:18px;line-height:18px;text-align:center;background:linear-gradient(180deg,#f8cf52,#e8a51c);border-radius:3px;font-size:10px;color:var(--white)}
.footer-link{font-size:9.5px;color:var(--footer-text);letter-spacing:.8px}
.social{width:20px;height:20px}
.legal{font-size:8.5px;color:var(--footer-text);letter-spacing:1px}
</style>
</head>
<body>

<div class="abs top-bar"></div>

<header class="abs header">
  <div class="abs brand-name">KELBRIDGE PAINTING</div>
  <div class="abs brand-tag">Quality Finishes Every Time</div>
  <nav class="nav">
    <a class="active" href="#">Home</a>
    <a style="left:344px" href="#">About us</a>
    <a style="left:439px" href="#">Services</a>
    <a style="left:530px" href="#">Testimonials</a>
    <a style="left:647px" href="#">Showcase</a>
    <a style="left:748px" href="#">Contact us</a>
  </nav>
</header>

<section class="abs hero" role="img" aria-label="Painter climbing a tall ladder against a blue cloudy sky above a field of red poppies">
  <div class="service" style="left:373px;top:58px">
    <div class="service-label">Residential</div>
    <div class="service-photo" role="img" aria-label="Yellow two-storey house" style="background:linear-gradient(180deg,#8fb6d9,#e8cf5a 60%,#5d8a3a)"></div>
  </div>
  <div class="service" style="left:528px;top:58px">
    <div class="service-label">Commercial</div>
    <div class="service-photo" role="img" aria-label="Worker facing colourful city buildings" style="background:linear-gradient(180deg,#3fa7d8,#e2744a 60%,#b84a5a)"></div>
  </div>
  <div class="service" style="left:683px;top:58px">
    <div class="service-label">Strata Jobs</div>
    <div class="service-photo" role="img" aria-label="Team of builders in hard hats" style="background:linear-gradient(180deg,#8a8070,#5c5a55 60%,#c9c27a)"></div>
  </div>

  <div class="abs welcome" style="top:236px">
    <div class="abs welcome-kicker">Welcome to</div>
    <div class="abs welcome-title">Kelbridge Painting</div>
    <div class="abs welcome-rule"></div>
    <p class="abs welcome-text">Lorem ipsum dolor sit amet, consectetur adipiscing elit. Aenean accumsan sollicitudin mi at vehicula. Praesent nisl mi, molestie eget rutrum eget, sodales ac nisl. Vivamus neque felis.</p>
  </div>

  <div class="abs dots" style="top:437px"><span></span><span></span><span></span><span></span></div>
</section>

<section class="abs testimonials">
  <h2 class="abs section-title">Client Testimonials</h2>
  <div class="abs section-rule"></div>

  <div class="abs quote-photo" role="img" aria-label="Portrait of a smiling woman" style="left:115px;top:78px;background:linear-gradient(135deg,#f3e4d6,#8a5a3c)"></div>
  <p class="abs quote-text" style="left:198px;top:78px">Lorem ipsum dolor sit amet, consectetur adipiscing elit. Aenean accumsan sollicitu-din mi at vehicula.Lorem ipsum dolor sit amet, consectetur adipiscing elit. Aenean</p>
  <div class="abs quote-author" style="left:195px;top:152px">- Jane Doe, &nbsp;Restaurant Owner</div>

  <div class="abs quote-photo" role="img" aria-label="Portrait of a smiling man with glasses" style="left:463px;top:78px;background:linear-gradient(135deg,#d9d6d0,#8a7058)"></div>
  <p class="abs quote-text" style="left:546px;top:78px">Lorem ipsum dolor sit amet, consectetur adipiscing elit. Aenean accumsan sollicitu-din mi at vehicula.Lorem ipsum dolor sit amet, consectetur adipiscing elit. Aenean</p>
  <div class="abs quote-author" style="left:545px;top:152px">- John Smith</div>
</section>

<section class="abs guarantee-area">
  <div class="abs guarantee">
    <div class="abs guarantee-head">
      <h2 class="abs guarantee-title">Satisfaction Guaranteed</h2>
    </div>
    <p class="abs guarantee-text">Lorem ipsum dolor sit amet, consectetur adipiscing elit. Aenean accumsan sollicitudin mi at vehicula. Praesent nisl mi, molestie eget rutrum eget, sodales ac nisl. vehicula. Praesent nisl mi, molestie eget rutrum eget, sodales ac nisl.</p>
    <div class="abs seal" role="img" aria-label="Gold guarantee seal"></div>
  </div>
</section>

<footer class="abs footer">
  <h3 class="abs footer-title" style="left:114px;top:18px">Newsletter</h3>
  <div class="abs footer-rule" style="left:114px;top:46px;width:161px"></div>
  <div class="abs field" style="left:115px;top:60px;width:103px;height:21px">Name</div>
  <div class="abs field" style="left:115px;top:88px;width:103px;height:21px">Email</div>
  <div class="abs field" style="left:115px;top:116px;width:144px;height:56px">Message</div>
  <div class="abs submit">Submit</div>

  <h3 class="abs footer-title" style="left:359px;top:18px">Navigation</h3>
  <div class="abs footer-rule" style="left:351px;top:46px;width:161px"></div>
  <span class="abs footer-link" style="left:359px;top:64px">Home</span>
  <span class="abs footer-link" style="left:450px;top:64px">Testimonials</span>
  <span class="abs footer-link" style="left:359px;top:98px">About</span>
  <span class="abs footer-link" style="left:450px;top:98px">Showcase</span>
  <span class="abs footer-link" style="left:359px;top:132px">Services</span>
  <span class="abs footer-link" style="left:450px;top:132px">Contact</span>

  <h3 class="abs footer-title" style="left:674px;top:18px">Follow us</h3>
  <div class="abs footer-rule" style="left:652px;top:46px;width:161px"></div>
  <div class="abs social" role="img" aria-label="Social link" style="left:679px;top:67px;background:#4fb0e0"></div>
  <div class="abs social" role="img" aria-label="Social link" style="left:705px;top:67px;background:#3b5a9a"></div>
  <div class="abs social" role="img" aria-label="Feed link" style="left:730px;top:67px;background:#f08a1c"></div>

  <span class="abs legal" style="left:359px;top:196px">Copyright @ 2013 Kelbridge Painting</span>
  <span class="abs legal" style="left:610px;top:197px">Sitemap &nbsp;&nbsp;| &nbsp;&nbsp;Terms &amp; Conditions &nbsp;&nbsp;| &nbsp;&nbsp;FAQ</span>
</footer>

</body>
</html>
```